Corporate Business Card

Very professional, Modern, Not to busy, include phone address email, website
(253) 617-4930, 18761 52nd Avenue S, Kent, WA 98047, martin@plumlinegroup.com, varkoworks.com

Target Market(s)

Manufacturing

Industry/Entity Type

Aero, machining, manufacturing, Off road racing

Contact Information for Business Card

Phone, address email, website

```html
<!DOCTYPE html>
<html lang="en">
<head>
<meta charset="utf-8">
<title>Varko Industries – Business Card</title>
<link rel="stylesheet" href="https://fonts.googleapis.com/css2?family=Exo+2:wght@500;700&display=swap">
<style>
  :root {
    --navy: #17346d;
    --navy-soft: #24457f;
    --red: #d8232a;
    --white: #ffffff;
  }
  html, body {
    margin: 0;
    padding: 0;
    overflow: hidden;
    background: var(--white);
  }
  .card {
    position: relative;
    width: 686px;
    height: 1200px;
    overflow: hidden;
    background: var(--white);
    font-family: "Exo 2", Arial, sans-serif;
    color: var(--navy);
  }
  .card-frame {
    position: absolute;
    inset: 0;
  }
  .brand-name {
    position: absolute;
    left: 0;
    right: 0;
    top: 296px;
    margin: 0;
    text-align: center;
    font-size: 118px;
    font-weight: 700;
    line-height: 1;
    letter-spacing: 12px;
    padding-left: 12px;
  }
  .brand-rule {
    position: absolute;
    left: 110px;
    top: 423px;
    width: 221px;
    height: 3px;
    background: var(--navy);
  }
  .brand-sub {
    position: absolute;
    right: 126px;
    top: 405px;
    margin: 0;
    font-size: 32px;
    font-weight: 700;
    line-height: 1;
  }
  .contact {
    position: absolute;
    left: 0;
    right: 0;
    top: 478px;
    margin: 0;
    padding: 0;
    list-style: none;
    text-align: center;
    font-size: 20px;
    font-weight: 500;
    line-height: 28px;
  }
  .pattern-panel {
    position: absolute;
    left: 0;
    top: 674px;
    width: 686px;
    height: 480px;
    background: linear-gradient(180deg, var(--navy-soft) 0%, var(--navy) 100%);
  }
</style>
</head>
<body>
<div class="card">
  <svg class="card-frame" width="686" height="1200" viewBox="0 0 686 1200" aria-hidden="true">
    <polygon class="corner corner-left" points="0,0 126,0 48,57 0,57" fill="var(--red)"/>
    <polygon class="corner corner-right" points="560,0 686,0 686,57 638,57" fill="var(--red)"/>
    <polyline class="frame-line frame-line-top" points="0,137 122,137 303,0" fill="none" stroke="var(--navy)" stroke-width="3"/>
    <polyline class="frame-line frame-line-top" points="383,0 563,137 686,137" fill="none" stroke="var(--navy)" stroke-width="3"/>
    <polyline class="frame-line frame-line-bottom" points="0,623 197,623 249,674" fill="none" stroke="var(--navy)" stroke-width="3"/>
    <polyline class="frame-line frame-line-bottom" points="437,674 489,623 686,623" fill="none" stroke="var(--navy)" stroke-width="3"/>
    <rect class="base-band" x="0" y="674" width="686" height="526" fill="var(--navy)"/>
    <rect class="base-stripe" x="0" y="1155" width="686" height="4" fill="var(--white)"/>
  </svg>

  <p class="brand-name">VARKO</p>
  <span class="brand-rule"></span>
  <p class="brand-sub">Industries</p>

  <ul class="contact">
    <li class="contact-phone">(253) 617-4930</li>
    <li class="contact-address">18761 52nd Avenue S, Kent, WA 98047</li>
    <li class="contact-email">martin@plumlinegroup.com</li>
    <li class="contact-web">varkoworks.com</li>
  </ul>

  <div class="pattern-panel" role="img" aria-label="Repeating company name pattern in soft navy tones"></div>
</div>
</body>
</html>
```